New National Dermatology Group needs a business card!

We need a business card for our new national company that has 3 brands within the business:
Lumora Clinics Australia, Tessaly Clinics Australia and Corvane Clinics Australia.
We help people access dermatology services close to home throughout Australia.
We need a business card that has:
all 3 logos on it,
Our websites (there are three, listed above)
Our email (there are three, listed above)
The location of our first clinic: 41 Willow Rd Parramatta (this can then be changed for each location as required)

```html
<!DOCTYPE html>
<html lang="en">
<head>
<meta charset="utf-8">
<title>Dermatology Group Business Card</title>
<link href="https://fonts.googleapis.com/css2?family=Open+Sans:wght@400;700&display=swap" rel="stylesheet">
<style>
  :root {
    --page: #2a2a2a;
    --card-dark: #050505;
    --card-light: #ffffff;
    --green: #1fa84a;
    --orange: #f07f2a;
    --orange-light: #f6a865;
    --brown: #8a4a26;
    --brown-light: #a8704a;
    --grey: #6b6b6b;
    --grey-dark: #555555;
  }
  * { box-sizing: border-box; margin: 0; padding: 0; }
  html, body { width: 1200px; height: 900px; overflow: hidden; }
  body {
    background: var(--page);
    font-family: "Open Sans", Arial, sans-serif;
    display: flex;
    flex-direction: column;
    align-items: center;
    justify-content: center;
    gap: 30px;
  }
  .card {
    width: 800px;
    height: 410px;
    position: relative;
    overflow: hidden;
    box-shadow: 0 8px 24px rgba(0,0,0,.5);
  }
  .card-front { background: var(--card-dark); }
  .card-back { background: var(--card-light); }

  .pattern-fill {
    position: absolute; inset: 0 0 14px 0;
    background: linear-gradient(90deg, #061a0d 0%, #050505 33%, #1a0e05 50%, #050505 66%, #150c07 100%);
  }

  .brand-band {
    position: absolute; left: 0; right: 0; bottom: 0; height: 14px;
    display: flex;
  }
  .brand-band span { flex: 1; }
  .brand-band .band-green { background: var(--green); }
  .brand-band .band-orange { background: linear-gradient(90deg, var(--orange), var(--orange-light)); }
  .brand-band .band-brown { background: linear-gradient(90deg, var(--brown-light), var(--brown)); }

  .brand-row {
    position: absolute; left: 0; right: 0;
    display: grid; grid-template-columns: repeat(3, 1fr);
    padding: 0 30px;
  }
  .card-front .brand-row { top: 170px; }
  .card-back .brand-row { top: 44px; }

  .brand-name {
    font-weight: 700;
    font-size: 15px;
    letter-spacing: 1.5px;
    text-transform: uppercase;
    text-align: center;
    line-height: 1.3;
  }
  .brand-green { color: var(--green); }
  .brand-orange { color: var(--orange); }
  .brand-brown { color: var(--brown); }

  .contact-row {
    position: absolute; left: 0; right: 0; top: 130px;
    display: grid; grid-template-columns: repeat(3, 1fr);
    padding: 0 30px 0 50px;
  }
  .person-name {
    font-weight: 700; font-size: 15px; text-transform: uppercase; letter-spacing: .3px;
  }
  .person-title { font-size: 14px; color: var(--grey); margin-top: -2px; }
  .divider { width: 26px; height: 2px; margin: 22px 0 24px; }
  .contact-list { list-style: none; }
  .contact-list li {
    display: flex; align-items: center; gap: 8px;
    font-size: 13px; color: var(--grey-dark); line-height: 22px;
  }
  .contact-list svg { width: 13px; height: 13px; flex: none; }
  .address { font-size: 13.5px; color: var(--grey); margin-top: 10px; }

  .col-green .person-name { color: var(--green); }
  .col-green .divider { background: var(--green); }
  .col-green svg { fill: var(--green); }
  .col-orange .person-name { color: var(--orange); }
  .col-orange .divider { background: var(--orange); }
  .col-orange svg { fill: var(--orange); }
  .col-brown .person-name { color: var(--brown); }
  .col-brown .divider { background: var(--brown); }
  .col-brown svg { fill: var(--brown-light); }
</style>
</head>
<body>

  <section class="card card-front">
    <div class="pattern-fill" role="img" aria-label="Faint repeating pattern of the three clinic names on black"></div>
    <div class="brand-row">
      <p class="brand-name brand-green">Lumora Clinics Australia</p>
      <p class="brand-name brand-orange">Tessaly Clinics Australia</p>
      <p class="brand-name brand-brown">Corvane Clinics Australia</p>
    </div>
    <div class="brand-band"><span class="band-green"></span><span class="band-orange"></span><span class="band-brown"></span></div>
  </section>

  <section class="card card-back">
    <div class="brand-row">
      <p class="brand-name brand-green">Lumora Clinics Australia</p>
      <p class="brand-name brand-orange">Tessaly Clinics Australia</p>
      <p class="brand-name brand-brown">Corvane Clinics Australia</p>
    </div>

    <div class="contact-row">
      <div class="contact-col col-green">
        <p class="person-name">Daniel Hartley</p>
        <p class="person-title">Manager</p>
        <div class="divider"></div>
        <ul class="contact-list">
          <li><svg viewBox="0 0 16 16"><path d="M3 1l3 3-1.5 2a9 9 0 0 0 5.5 5.5L12 10l3 3-2 2C7 15 1 9 1 3z"/></svg>555-014-2100</li>
          <li><svg viewBox="0 0 16 16"><path d="M1 3h14v10H1z M1 3l7 6 7-6" stroke="#fff" stroke-width="1.2"/></svg>hello@lumoraclinics.au</li>
          <li><svg viewBox="0 0 16 16"><circle cx="8" cy="8" r="7"/></svg>www.lumoraclinics.au</li>
        </ul>
        <p class="address">41 Willow Rd Parramatta</p>
      </div>
      <div class="contact-col col-orange">
        <p class="person-name">Daniel Hartley</p>
        <p class="person-title">Manager</p>
        <div class="divider"></div>
        <ul class="contact-list">
          <li><svg viewBox="0 0 16 16"><path d="M3 1l3 3-1.5 2a9 9 0 0 0 5.5 5.5L12 10l3 3-2 2C7 15 1 9 1 3z"/></svg>555-014-2100</li>
          <li><svg viewBox="0 0 16 16"><path d="M1 3h14v10H1z M1 3l7 6 7-6" stroke="#fff" stroke-width="1.2"/></svg>hello@tessalyclinics.au</li>
          <li><svg viewBox="0 0 16 16"><circle cx="8" cy="8" r="7"/></svg>www.tessalyclinics.au</li>
        </ul>
        <p class="address">41 Willow Rd Parramatta</p>
      </div>
      <div class="contact-col col-brown">
        <p class="person-name">Daniel Hartley</p>
        <p class="person-title">Manager</p>
        <div class="divider"></div>
        <ul class="contact-list">
          <li><svg viewBox="0 0 16 16"><path d="M3 1l3 3-1.5 2a9 9 0 0 0 5.5 5.5L12 10l3 3-2 2C7 15 1 9 1 3z"/></svg>555-014-2100</li>
          <li><svg viewBox="0 0 16 16"><path d="M1 3h14v10H1z M1 3l7 6 7-6" stroke="#fff" stroke-width="1.2"/></svg>hello@corvaneclinics.au</li>
          <li><svg viewBox="0 0 16 16"><circle cx="8" cy="8" r="7"/></svg>www.corvaneclinics.au</li>
        </ul>
        <p class="address">41 Willow Rd Parramatta</p>
      </div>
    </div>

    <div class="brand-band"><span class="band-green"></span><span class="band-orange"></span><span class="band-brown"></span></div>
  </section>

</body>
</html>
```